Meridale Bed Company Needs Business Card

Looking for a very nice looking business card. Creative but not extravagant. We sell beds and pillows across the U.S. and need something professional but catchy. I have attached the logo.

Name : Devin Holt
Title : President
Phone : (800) 471-2960
Email: sleep@quilmora.com
Website: www.quilmora.com

Can be single-sided or double-sided
horizontal or vertical

Can use Blues/Greys

Target Market(s)

Mass Market

Industry/Entity Type

Retail

Contact Information for Business Card

Name : Devin Holt
Title : President
Phone : (800) 471-2960
Email: sleep@quilmora.com
Website: www.quilmora.com

Requirements
Must have
• Clean, Modern, Smooth
• Can use Blues/Greys
• On the other side without the information - have something simple like www.quilmora.com or our logo
Nice to have
• Surprise me
Should not have
• Nothing crazy, nothing cluttered

```html
<!DOCTYPE html>
<html lang="en">
<head>
<meta charset="utf-8">
<title>Quilmora Business Card</title>
<link href="https://fonts.googleapis.com/css2?family=Arimo:wght@400;700&display=swap" rel="stylesheet">
<style>
  :root {
    --backdrop: #2c2724;
    --card: #24282d;
    --card-edge: #1b1e22;
    --wordmark-grey: #a9acb0;
    --wordmark-blue: #3aa4e0;
    --name-blue: #2f95d6;
    --text-light: #e6e8ea;
    --icon-blue: #2f95d6;
  }
  html, body {
    margin: 0;
    width: 1200px;
    height: 769px;
    overflow: hidden;
    background: var(--backdrop);
    font-family: "Arimo", Arial, sans-serif;
  }
  .stage {
    position: relative;
    width: 1200px;
    height: 769px;
    display: flex;
    align-items: center;
    justify-content: center;
    gap: 48px;
  }
  .card {
    position: relative;
    width: 520px;
    height: 297px;
    background: var(--card);
    border-radius: 4px;
    box-shadow: 0 2px 0 var(--card-edge), 0 18px 40px rgba(0,0,0,.45);
    overflow: hidden;
  }
  .card-front {
    display: flex;
    align-items: center;
    justify-content: center;
  }
  .wordmark {
    font-family: "Arimo", Arial, sans-serif;
    font-weight: 400;
    letter-spacing: 0;
    line-height: 1;
    white-space: nowrap;
  }
  .card-front .wordmark {
    font-size: 64px;
    color: var(--wordmark-grey);
  }
  .card-back .wordmark {
    position: absolute;
    top: 78px;
    left: 0;
    right: 0;
    text-align: center;
    font-size: 58px;
    color: var(--wordmark-blue);
  }
  .details {
    position: absolute;
    top: 180px;
    left: 0;
    right: 0;
    display: flex;
    justify-content: center;
    align-items: stretch;
    gap: 16px;
  }
  .person {
    text-align: right;
    padding-top: 4px;
  }
  .person-name {
    font-weight: 700;
    font-size: 17px;
    color: var(--name-blue);
  }
  .person-title {
    font-weight: 400;
    font-size: 15px;
    color: var(--text-light);
    margin-top: 3px;
  }
  .divider {
    width: 1px;
    background: var(--text-light);
    opacity: .8;
  }
  .contact {
    list-style: none;
    margin: 0;
    padding: 2px 0;
  }
  .contact li {
    display: flex;
    align-items: center;
    gap: 8px;
    font-weight: 400;
    font-size: 14px;
    color: var(--text-light);
    line-height: 22px;
  }
  .contact svg {
    width: 13px;
    height: 13px;
    fill: var(--icon-blue);
    flex: none;
  }
</style>
</head>
<body>
<main class="stage">
  <section class="card card-front" aria-label="Card front">
    <div class="wordmark">quilmora</div>
  </section>

  <section class="card card-back" aria-label="Card back">
    <div class="wordmark">quilmora</div>
    <div class="details">
      <div class="person">
        <div class="person-name">Devin Holt</div>
        <div class="person-title">President</div>
      </div>
      <div class="divider"></div>
      <ul class="contact">
        <li>
          <svg viewBox="0 0 16 16" aria-hidden="true"><path d="M3.6 1.2l2.3 2.3c.4.4.4 1 0 1.4L4.8 6c.8 1.9 2.3 3.4 4.2 4.2l1.1-1.1c.4-.4 1-.4 1.4 0l2.3 2.3c.4.4.4 1 0 1.4l-1.3 1.3c-.6.6-1.5.8-2.3.5C5.9 13.2 2.8 10.1 1.4 5.8c-.3-.8-.1-1.7.5-2.3z"/></svg>
          (800) 471-2960
        </li>
        <li>
          <svg viewBox="0 0 16 16" aria-hidden="true"><path d="M1 3h14v1.2L8 8.6 1 4.2z"/><path d="M1 5.6l7 4.4 7-4.4V13H1z"/></svg>
          sleep@quilmora.com
        </li>
        <li>
          <svg viewBox="0 0 16 16" aria-hidden="true"><path d="M8 1a7 7 0 1 0 0 14A7 7 0 0 0 8 1zm0 1.6c.9 0 1.8 1.9 2 4.6H6c.2-2.7 1.1-4.6 2-4.6zM6 8.8h4c-.2 2.7-1.1 4.6-2 4.6s-1.8-1.9-2-4.6z"/></svg>
          www.quilmora.com
        </li>
      </ul>
    </div>
  </section>
</main>
</body>
</html>
```